The Polish & Glow Studio Website Update

Hello. I am seeking to freshen up my website with a clean and easy feel that incorporates our modern chic style. Our services cater to mostly young professionals and modern moms.

We focus on natural nail care and gentle professional waxing. We are known for our cleanliness. Our clients like our current website, however I'm hoping to make it look even more professional and user friendly. Some clients have even said our current website feels welcoming, unlike other websites that in they feel give a snobbish vibe. I like clean lines, simple, fresh, and sometimes bold. Totally NOT a fan of whimsical.

I threw added an accent color to the color pallet...however it should be used in moderation. I am also open to other accent colors. I'd like the site to emphasize the Brazilian wax as much as nails, if not more than nail. The photos downloaded are just to give you a few images of who we are, however are not necessary. Current website www.thepolishandglowstudio.example

Target Market(s)

Females 30-55

Industry/Entity Type

Beauty Salon

Coding

Coded - Design and coding required

Number of Pages Required

5+ page

Font styles to use
Sans Serif

Colors
ffffff
1b1b1b
acd136
eeeeee
878787
c4c4c4
efefef
7f7f7f

Requirements
Must have
• Clean look
Nice to have
• Our logo
Should not have
• Whimsical

```html
<!DOCTYPE html>
<html lang="en">
<head>
<meta charset="utf-8">
<title>The Polish &amp; Glow Studio</title>
<link href="https://fonts.googleapis.com/css2?family=Questrial&family=Open+Sans:wght@400;600&display=swap" rel="stylesheet">
<style>
:root{
  --white:#ffffff;
  --ink:#1b1b1b;
  --lime:#acd136;
  --lime-dark:#8fb822;
  --mist:#eeeeee;
  --mist-2:#efefef;
  --grey:#878787;
  --grey-2:#7f7f7f;
  --line:#c4c4c4;
  --footer-bar:#7a9a22;
}
*{margin:0;padding:0;box-sizing:border-box}
html,body{width:841px;height:1200px;overflow:hidden;background:var(--white)}
body{position:relative;font-family:"Open Sans",sans-serif;color:var(--ink)}
.display{font-family:"Questrial",sans-serif}
.abs{position:absolute}
.accent{color:var(--lime)}
.btn{position:absolute;display:flex;align-items:center;justify-content:center;background:linear-gradient(#b9da4a,#97c02a);color:var(--white);font-family:"Questrial",sans-serif;font-size:8px;letter-spacing:.2px;border-radius:2px;text-transform:uppercase;white-space:nowrap}

.top-rule{left:0;top:0;width:841px;height:2px;background:var(--lime)}
.brand{left:90px;top:28px;font-family:"Questrial",sans-serif;color:var(--grey-2);font-size:21px;line-height:1.05}
.brand small{display:block;font-size:11px;letter-spacing:.5px}
.contact-item{top:38px;display:flex;align-items:center;gap:8px;font-size:8.5px;color:var(--ink);white-space:nowrap}
.contact-item .dot{width:19px;height:19px;border-radius:50%;background:var(--ink);display:flex;align-items:center;justify-content:center;flex:none}

.nav{left:0;top:92px;width:841px;height:38px;background:linear-gradient(#2a2a2a,#0e0e0e)}
.nav a{position:absolute;top:0;height:38px;display:flex;align-items:center;color:var(--white);font-family:"Questrial",sans-serif;font-size:8.5px;text-decoration:none;text-transform:uppercase;white-space:nowrap}
.nav .active{background:var(--lime);justify-content:center;left:93px;width:65px}
.nav .divider{position:absolute;top:0;width:1px;height:38px;background:#3a3a3a}

.hero{left:0;top:130px;width:841px;height:326px;background:linear-gradient(100deg,#ece9e4 0%,#e6e1db 45%,#d9c3b6 62%,#cfa596 80%,#e2d8d0 100%)}
.hero-curve{left:0;top:410px}
.hero-title{left:92px;top:196px;font-size:21px;line-height:25px;color:var(--ink);text-transform:uppercase;white-space:nowrap}
.hero-text{left:93px;top:256px;width:280px;font-size:7.6px;line-height:13.5px}
.slider-dots{left:93px;top:371px;display:flex;gap:6px}
.slider-dots span{width:8px;height:8px;border-radius:50%;background:var(--white)}
.slider-dots span:first-child{background:var(--lime)}

.section-title{font-size:21px;text-transform:uppercase;color:var(--ink);white-space:nowrap}
.services-title{left:0;width:841px;top:474px;text-align:center}
.service{position:absolute;top:538px;width:160px;height:160px;border-radius:50%;background:var(--mist);text-align:center;padding-top:38px}
.service h3{font-family:"Questrial",sans-serif;font-weight:400;font-size:10.5px;text-transform:uppercase}
.service .rule{width:32px;height:1px;background:var(--ink);margin:9px auto 11px}
.service p{font-size:7.6px;line-height:14px;padding:0 8px}
.service .more{display:inline-block;margin-top:7px;border:1px solid var(--ink);border-radius:10px;padding:3px 7px;font-family:"Questrial",sans-serif;font-size:7.6px;text-transform:uppercase}
.service.featured{background:linear-gradient(#b8d94a,#96bf28);color:var(--white)}
.service.featured .rule{background:var(--white)}
.service.featured .more{border-color:var(--white)}
.service-icon{position:absolute;top:514px;width:46px;height:46px;border-radius:50%;background:var(--lime);border:2px solid var(--white);display:flex;align-items:center;justify-content:center}
.service-icon.dark{background:var(--ink)}

.mission{left:0;top:729px;width:841px;height:261px;background:linear-gradient(var(--mist) 0%,var(--white) 40%);border-top:1px solid #dcdcdc}
.mission-title{left:91px;top:772px}
.mission-text{left:93px;top:805px;width:379px;font-size:7.6px;line-height:13.6px;text-align:justify}
.mission-text p+p{margin-top:13.6px}
.mission-photo{left:488px;top:777px;width:259px;height:182px;border:1px solid #d6d6d6;background:var(--white);padding:3px}
.mission-photo div{width:100%;height:100%;background:linear-gradient(#cfcbc4 0%,#b7b2aa 45%,#6e8a4c 60%,#5a7343 72%,#e8e8e8 100%)}

.footer{left:0;top:990px;width:841px;height:170px;background:linear-gradient(#b9da4c,#9cc42e)}
.footer h4{position:absolute;top:22px;font-family:"Questrial",sans-serif;font-weight:400;font-size:10px;color:var(--white);text-transform:uppercase}
.footer ul{position:absolute;top:43px;list-style:none;font-size:7.6px;line-height:14.5px;color:var(--white);white-space:nowrap}
.footer-brand{left:579px;top:26px;font-family:"Questrial",sans-serif;color:var(--white);font-size:30px;line-height:1;white-space:nowrap}
.footer-brand small{display:block;font-size:12px;text-align:right;letter-spacing:1px}
.footer-bar{left:0;top:1160px;width:841px;height:40px;background:var(--footer-bar);color:var(--white);font-size:7.6px;display:flex;align-items:center;padding-left:93px}
.social{right:100px;top:1173px;display:flex;gap:6px}
.social span{width:13px;height:13px;border-radius:50%;background:var(--white);opacity:.9}
</style>
</head>
<body>
<div class="abs top-rule"></div>

<header>
  <div class="abs brand">The Polish &amp; Glow<small>Studio</small></div>
  <div class="abs contact-item" style="left:346px">
    <span class="dot"><svg width="9" height="9" viewBox="0 0 24 24"><path fill="#fff" d="M6.6 10.8a15 15 0 006.6 6.6l2.2-2.2c.3-.3.7-.4 1-.2 1.1.4 2.3.6 3.6.6.6 0 1 .4 1 1V20c0 .6-.4 1-1 1C10.6 21 3 13.4 3 4c0-.6.4-1 1-1h3.5c.6 0 1 .4 1 1 0 1.3.2 2.5.6 3.6.1.3 0 .7-.2 1z"/></svg></span>
    (555) 014-2270
  </div>
  <div class="abs contact-item" style="left:445px">
    <span class="dot"><svg width="9" height="8" viewBox="0 0 24 20"><path fill="#fff" d="M2 2h20v16H2z"/><path d="M2 3l10 8 10-8" stroke="#1b1b1b" stroke-width="2" fill="none"/></svg></span>
    info@polishandglow.example
  </div>
  <div class="btn" style="left:609px;top:30px;width:139px;height:33px">Schedule an appointment</div>
</header>

<nav class="abs nav">
  <a class="active" href="#">Home</a>
  <a href="#" style="left:178px">About us</a>
  <span class="divider" style="left:241px"></span>
  <a href="#" style="left:262px">Products and services</a>
  <span class="divider" style="left:383px"></span>
  <a href="#" style="left:403px">Specials</a>
  <span class="divider" style="left:459px"></span>
  <a href="#" style="left:483px">Careers</a>
  <span class="divider" style="left:542px"></span>
  <a href="#" style="left:562px">Contact us</a>
</nav>

<section>
  <div class="abs hero" role="img" aria-label="Close-up of a hand with natural French manicure resting on a white towel"></div>
  <svg class="abs hero-curve" width="841" height="50" viewBox="0 0 841 50"><path d="M0 12 Q420 70 841 12 L841 50 L0 50 Z" fill="#fff"/></svg>
  <h1 class="abs hero-title display" style="font-weight:400">Advanced <span class="accent">techniques</span>, and<br>exceptional <span class="accent">sanitation</span></h1>
  <p class="abs hero-text">Our knowledgeable and friendly staff is always happy to assist with any of your Polish &amp; Glow concerns.</p>
  <div class="btn" style="left:93px;top:310px;width:135px;height:33px">Schedule an appointment</div>
  <div class="abs slider-dots"><span></span><span></span><span></span><span></span></div>
</section>

<section>
  <h2 class="abs section-title services-title display" style="font-weight:400">Our <span class="accent">services</span></h2>

  <div class="service" style="left:125px">
    <h3>LuxeGel manicures</h3><div class="rule"></div>
    <p>Maintain your beautiful LuxeGel Manicure and save with this series of 6 Luxe LuxeGel Manicures</p>
    <span class="more">Read more</span>
  </div>
  <div class="service featured" style="left:340px">
    <h3>Brazilian waxes</h3><div class="rule"></div>
    <p>Maintain your beautiful LuxeGel Manicure and save with this series of 6 Luxe LuxeGel Manicures</p>
    <span class="more">Read more</span>
  </div>
  <div class="service" style="left:554px">
    <h3>Chemical peel</h3><div class="rule"></div>
    <p>Maintain your beautiful LuxeGel Manicure and save with this series of 6 Luxe LuxeGel Manicures</p>
    <span class="more">Read more</span>
  </div>

  <div class="service-icon" style="left:182px"><svg width="20" height="22" viewBox="0 0 20 22"><rect x="3" y="8" width="8" height="11" rx="2" fill="#fff"/><rect x="5" y="4" width="4" height="4" fill="#fff"/><rect x="14" y="2" width="2" height="12" fill="#fff"/><rect x="13" y="14" width="4" height="6" rx="1" fill="#fff"/></svg></div>
  <div class="service-icon dark" style="left:397px"><svg width="16" height="22" viewBox="0 0 16 22"><path d="M3 21V8a5 5 0 0110 0v13z" fill="#fff"/><path d="M6 18V9" stroke="#1b1b1b" stroke-width="1.5"/></svg></div>
  <div class="service-icon" style="left:611px"><svg width="24" height="20" viewBox="0 0 24 20"><path d="M9 2c2 3 3 4.5 3 6a3 3 0 01-6 0c0-1.5 1-3 3-6z" fill="#fff"/><path d="M2 14h7l4 2h7l2-3-9 1-4-2H2z" fill="#fff"/></svg></div>
</section>

<section>
  <div class="abs mission"></div>
  <h2 class="abs section-title mission-title display" style="font-weight:400">Our <span class="accent">mission</span></h2>
  <div class="abs mission-text">
    <p>To be the #1 nail and wax salon in the Fairhaven, CT area, offering the most meticulous manicures, pedicures, and waxing service. We use superior products, advanced techniques, and exceptional sanitation procedures to provide our clients with safe, quality services. Our knowledgeable and friendly staff is always happy to assist with any of your Polish &amp; Glow concerns.</p>
    <p>We are excited to welcome another Licensed Nail Technician to our team, Clara Whitfield. Clara has over 25 years experience and is also a certified Medical Nail Technician. You will love her spunk and genuine friendliness. If you're seeking a perfect mani, Clara is your girl.</p>
  </div>
  <div class="btn" style="left:93px;top:929px;width:69px;height:26px">Read more</div>
  <div class="abs mission-photo"><div role="img" aria-label="Treatment room with a waxing bed draped in a green sheet and dark cabinets"></div></div>
</section>

<footer>
  <div class="abs footer">
    <h4 style="left:93px">Quick links</h4>
    <ul style="left:93px"><li>Home</li><li>Products</li><li>Careers</li><li>Specials</li><li>About Us</li><li>FAQ</li><li>Contact Us</li></ul>
    <h4 style="left:210px">Menu</h4>
    <ul style="left:210px"><li>Nails</li><li>Signature Manicure</li><li>Luxe LuxeGel Manicure</li><li>Signature Pedicure</li><li>~Wax~</li><li>Brow Design</li><li>Chin</li></ul>
    <ul style="left:319px;line-height:18px;top:41px"><li>Lip</li><li>Brazilian $55</li><li>Men Welcomed</li></ul>
    <h4 style="left:406px">Contact us</h4>
    <ul style="left:406px"><li>The Polish &amp; Glow Studio, 42 Elm Lane</li><li>Fairhaven, CT 06500</li><li>&nbsp;</li><li>ph: (555) 014-2270</li><li>info@polishandglow.example</li></ul>
    <div class="abs footer-brand">Polish &amp; Glow<small>Studio</small></div>
  </div>
  <div class="abs footer-bar">© 2016&nbsp; thepolishandglowstudio.example.&nbsp; All right reserved&nbsp; Term of Use</div>
  <div class="abs social"><span></span><span></span><span></span><span></span></div>
</footer>
</body>
</html>
```